Website Design for my Copper Distillation Equipment Business Nature Sciencey Theme

I already have a website www.cascobrewworks.com and its a sitevelo website builder one. But I cannot get the design right at all. I need this fixed.

I have logo. I need a redesign, for my website, the home page, that maybe I can have something similar in design- I can use as template to copy, for other pages so the whole thing matches? Look at my website so you understand I have a few pages...but most are links. Its a competition. Code has to be easy for me to implement, I am not expert.

Your advice needed..It would be a plus if I can update this myself throughout time. If I could have this explained to me too, the maintenance of it...how would I do this too..etc..pretend I am a child when you explain, if you can. I am not good with this stuff but I am smart and can learn fast.

I want a high end look. Maybe like an ivy league college-y look too, real preppy, chemistry...science-y, nature like is good, leaves, drops water, fields of wheat, lavender, etc.

I want every page to look similar, but the home page is what I want to be the main showpiece,..and I want each page have a little text section, maybe a photos section and a video section, for that market. Like a nice website. If I am not doing this right, let me know. I can work with you. Just help me, please. Let me know if I am doing this right.

When I pick my winning design, for my website, I will hire the artist one-on-one to re-design my shopping cart next. Or if I need additional help with implementing this current design, I can hire the same artist again too. I have a blog that I may want to hire the redesign as well too, but later on. My point is I am not just looking for one project here but I want to follow up with winning artist. So it would be return business for the winner.

I got my logo done here so I am repeat customer. And I have given that winning artist other design work.

Target Market(s)

Moonshine Stills I sell most, Essential Oil Business, Micro and Craft Distilleries, Canna-businesses, Alcohol Fuel

Industry/Entity Type

Business

Number of Pages Required

5+ page

Colors
ec1f27

Requirements
Must have
• The categories for the stills must be prominent and eye catching. The main photo I would like to be naturelike theme, but you can try out different things with me. I am open to ideas and suggestions. I would like this to be implemented easy and fast.
Nice to have
• My logo in it. You can use any of my photos as well from my pictoshare account. https://www.pictoshare.com/photos/81724596@K09/
• Colors of my Logo...matching design.
• Maybe some basic stock photos you see would match for me..
• Chemistry like symbols for the categories, I love that.

```html
<!DOCTYPE html>
<html lang="en">
<head>
<meta charset="utf-8">
<title>Casco Brew Works – Home</title>
<link href="https://fonts.googleapis.com/css2?family=Lato:ital,wght@0,400;0,700;1,400;1,700;1,900&display=swap" rel="stylesheet">
<style>
:root{
  --maroon:#4a1214;
  --maroon-text:#5a1a1c;
  --red:#b3141b;
  --page:#f7f7f7;
  --white:#ffffff;
  --ink:#333333;
  --muted:#666666;
  --footer:#1d1d1d;
  --footer-line:#555555;
  --footer-text:#d8d8d8;
}
*{box-sizing:border-box;margin:0;padding:0}
html,body{width:682px;height:1200px;overflow:hidden}
body{font-family:'Lato',sans-serif;background:var(--page);position:relative;color:var(--ink)}
.abs{position:absolute}

/* header */
.site-header{left:0;top:0;width:682px;height:58px;background:var(--white);border-bottom:3px solid var(--maroon)}
.brand{left:108px;top:5px;display:flex;align-items:center;gap:5px}
.brand-mark{width:12px;height:12px;background:var(--maroon);border-radius:50%}
.brand-name{font-size:13px;font-weight:700;color:var(--maroon);letter-spacing:.3px}
.top-btn{top:11px;height:15px;background:var(--maroon);color:var(--white);font-size:7px;display:flex;align-items:center;justify-content:center}
.btn-register{left:388px;width:53px}
.btn-login{left:457px;width:45px}
.btn-cart{left:513px;width:64px;justify-content:flex-start;padding-left:6px}
.btn-cart .cart-split{position:absolute;right:0;top:0;width:17px;height:15px;border-left:1px solid #7a3a3c;display:flex;align-items:center;justify-content:center}
.main-nav{right:105px;top:41px;display:flex;gap:10px;font-size:6.5px;color:var(--maroon-text)}

/* hero */
.hero{left:0;top:61px;width:682px;height:305px;background:linear-gradient(120deg,#5f7a2c 0%,#8ea84a 35%,#3e5a1d 60%,#9bb25a 100%)}

/* categories */
.category-band{left:0;top:366px;width:682px;height:60px;background:var(--maroon)}
.category-title{left:0;top:374px;width:682px;text-align:center;color:var(--white);font-size:9px;font-style:italic;font-weight:700}
.category{top:398px;width:70px;text-align:center}
.category svg{display:block;margin:0 auto}
.category-label{display:block;margin-top:14px;font-size:9.5px;color:var(--maroon-text)}
.slide-arrow{top:417px}

.rule{left:199px;top:485px;width:280px;height:2px;background:var(--maroon)}
.welcome-title{left:0;top:497px;width:682px;text-align:center;font-size:16px;font-style:italic;font-weight:900;color:var(--maroon);text-shadow:1px 1px 1px rgba(0,0,0,.25)}
.welcome-text{left:104px;top:522px;width:474px;text-align:center;font-size:6.3px;line-height:15px;color:var(--ink)}

.section-divider{left:0;width:682px;height:1px;background:#dcdcdc}

/* products */
.section-title{font-size:14.5px;font-style:italic;color:var(--maroon);font-weight:400}
.product-title{left:0;top:624px;width:682px;text-align:center}
.product-underline{left:305px;top:643px;width:72px;height:2px;background:var(--maroon)}
.product-card{top:672px;width:108px}
.product-image{width:108px;height:103px;border:1px solid #cfcfcf}
.product-name{font-size:7px;color:var(--maroon-text);margin-top:3px}
.product-desc{font-size:5.3px;color:var(--muted);line-height:9px;margin-top:1px}
.product-actions{display:flex;height:18px;margin-top:4px;background:var(--maroon);color:var(--white);font-size:6px;font-style:italic;font-weight:700}
.product-actions span{flex:1;display:flex;align-items:center;justify-content:center;gap:3px}
.product-actions span+span{border-left:1px solid #7a3a3c;flex:1.3}

/* media */
.block-title{top:870px}
.block-line{top:893px;height:1px;background:var(--maroon)}
.block-line::before{content:"";position:absolute;left:0;top:-1px;width:38px;height:3px;background:var(--maroon)}
.mini-arrows{top:882px;display:flex;gap:2px}
.video{top:904px;width:149px;height:104px;background:linear-gradient(160deg,#7b6a55,#a08c72 50%,#5d5347)}
.video-caption{position:absolute;left:0;top:0;width:100%;height:11px;background:rgba(0,0,0,.55);color:var(--white);font-size:5px;padding:3px 8px}
.video-play{position:absolute;left:63px;top:44px;width:22px;height:15px;background:#d8232a;border-radius:4px}
.video-play::after{content:"";position:absolute;left:8px;top:4px;border-left:7px solid #fff;border-top:3.5px solid transparent;border-bottom:3.5px solid transparent}
.video-bar{position:absolute;left:0;bottom:0;width:100%;height:8px;background:#222}
.video-bar i{position:absolute;left:28px;top:3px;width:42px;height:2px;background:#d8232a}
.blog-item{left:429px;width:148px;height:46px}
.blog-thumb{position:absolute;left:0;top:0;width:55px;height:46px}
.blog-text{position:absolute;left:62px;top:0;width:86px}
.blog-text b{display:block;font-size:5.8px;font-style:italic;color:var(--maroon-text);margin-bottom:3px}
.blog-text p{font-size:6px;line-height:10.5px;color:var(--muted);text-align:justify}

/* footer */
.site-footer{left:0;top:1040px;width:682px;height:160px;background:var(--footer)}
.footer-col{top:1057px;width:108px}
.footer-title{font-size:11.5px;font-style:italic;color:var(--white);height:16px}
.footer-line{height:1px;background:var(--footer-line);position:relative;margin-top:4px}
.footer-line::before{content:"";position:absolute;left:0;top:-1px;width:27px;height:3px;background:var(--white)}
.links{display:grid;grid-template-columns:57px 50px;margin-top:8px;font-size:6.2px;color:var(--footer-text);row-gap:8px}
.links span::before{content:"» "}
.footer-note{font-size:5.3px;color:#9a9a9a;line-height:11px;margin-top:6px}
.field{width:90px;height:14px;border:1px solid #999;background:#4a4a4a;color:#ddd;font-size:5.3px;font-style:italic;padding:3px 4px;margin-top:8px}
.subscribe{width:46px;height:14px;background:#d8d8d8;color:#333;font-size:5.8px;font-style:italic;display:flex;align-items:center;justify-content:center;margin-top:9px}
.news{display:flex;gap:6px;margin-top:7px}
.news-date{width:32px;height:28px;flex:none;background:#f2f2f2;text-align:center}
.news-date b{display:block;font-size:12px;color:#333;height:17px;line-height:17px}
.news-date span{display:block;background:var(--red);color:#fff;font-size:6px;height:11px;line-height:11px}
.news-text b{display:block;font-size:5px;color:#fff}
.news-text p{font-size:5px;color:#9a9a9a;line-height:9.5px}
.phone{display:flex;align-items:center;gap:4px;font-size:8.5px;color:var(--white);margin-top:6px}
.socials{display:flex;gap:8px;margin-top:10px}
.socials i{width:16px;height:16px;background:var(--white)}
</style>
</head>
<body>

<header class="abs site-header">
  <div class="abs brand"><span class="brand-mark"></span><span class="brand-name">Casco Brew Works</span></div>
  <div class="abs top-btn btn-register">Register</div>
  <div class="abs top-btn btn-login">Login</div>
  <div class="abs top-btn btn-cart">Add to Cart
    <span class="cart-split"><svg width="7" height="6" viewBox="0 0 7 6"><path d="M0 0h1.5l.8 3.5h3.5L7 1H2" fill="none" stroke="#fff" stroke-width=".8"/><circle cx="2.8" cy="5.3" r=".6" fill="#fff"/><circle cx="5.5" cy="5.3" r=".6" fill="#fff"/></svg></span>
  </div>
  <nav class="abs main-nav"><span>Home</span><span>About Us</span><span>Contact Us</span><span>Photos</span><span>Videos</span><span>Shop</span><span>Blog</span><span>Books</span><span>Links</span></nav>
</header>

<div class="abs hero" role="img" aria-label="Photo of a distiller gathering fresh green herbs into tubs in a leafy garden"></div>

<div class="abs category-band"></div>
<div class="abs category-title">Please Choose the Category of the Still you are looking for...</div>

<svg class="abs slide-arrow" style="left:92px" width="12" height="18" viewBox="0 0 12 18"><path d="M10 2L3 9l7 7" fill="none" stroke="#fff" stroke-width="3"/></svg>
<svg class="abs slide-arrow" style="left:579px" width="12" height="18" viewBox="0 0 12 18"><path d="M2 2l7 7-7 7" fill="none" stroke="#fff" stroke-width="3"/></svg>

<div class="abs category" style="left:106px">
  <svg width="46" height="50" viewBox="0 0 46 50"><polygon points="23,1 44,13 44,37 23,49 2,37 2,13" fill="#4a1214" stroke="#fff" stroke-width="2.5"/><g fill="#fff"><rect x="15" y="16" width="3" height="18"/><rect x="21" y="14" width="4" height="20"/><rect x="28" y="16" width="3" height="18"/><rect x="13" y="15" width="20" height="1.5"/></g></svg>
  <span class="category-label">Stills</span>
</div>
<div class="abs category" style="left:184px">
  <svg width="46" height="50" viewBox="0 0 46 50"><polygon points="23,1 44,13 44,37 23,49 2,37 2,13" fill="#4a1214" stroke="#fff" stroke-width="2.5"/><path d="M23 14c5 7 8 11 8 15a8 8 0 0 1-16 0c0-4 3-8 8-15z" fill="#fff"/><path d="M19 29a4 4 0 0 0 4 4" stroke="#4a1214" stroke-width="1.5" fill="none"/></svg>
  <span class="category-label">Essential Oils</span>
</div>
<div class="abs category" style="left:265px">
  <svg width="46" height="50" viewBox="0 0 46 50"><polygon points="23,1 44,13 44,37 23,49 2,37 2,13" fill="#4a1214" stroke="#fff" stroke-width="2.5"/><rect x="15" y="15" width="16" height="20" rx="2" fill="#fff"/><rect x="15" y="19" width="16" height="1.5" fill="#4a1214"/><rect x="15" y="30" width="16" height="1.5" fill="#4a1214"/><path d="M23 22c2 3 3 4 3 5a3 3 0 0 1-6 0c0-1 1-2 3-5z" fill="#4a1214"/></svg>
  <span class="category-label">Alcohol Fuel</span>
</div>
<div class="abs category" style="left:347px">
  <svg width="46" height="50" viewBox="0 0 46 50"><polygon points="23,1 44,13 44,37 23,49 2,37 2,13" fill="#4a1214" stroke="#fff" stroke-width="2.5"/><g fill="none" stroke="#fff" stroke-width="1.4"><path d="M23 36V22"/><path d="M23 22l-5-6M23 22l5-6M23 22V14M23 26l-7-3M23 26l7-3"/><circle cx="23" cy="20" r="6"/></g></svg>
  <span class="category-label">Cannabis</span>
</div>
<div class="abs category" style="left:428px">
  <svg width="46" height="50" viewBox="0 0 46 50"><polygon points="23,1 44,13 44,37 23,49 2,37 2,13" fill="#4a1214" stroke="#fff" stroke-width="2.5"/><rect x="17" y="14" width="12" height="19" rx="3" fill="none" stroke="#fff" stroke-width="1.8"/><rect x="20" y="18" width="6" height="4" fill="#fff"/><path d="M23 33v4M21 37h4" stroke="#fff" stroke-width="1.5"/></svg>
  <span class="category-label">Boilers</span>
</div>
<div class="abs category" style="left:508px">
  <svg width="46" height="50" viewBox="0 0 46 50"><polygon points="23,1 44,13 44,37 23,49 2,37 2,13" fill="#4a1214" stroke="#fff" stroke-width="2.5"/><rect x="21" y="12" width="4" height="18" rx="2" fill="none" stroke="#fff" stroke-width="1.5"/><circle cx="23" cy="33" r="4" fill="#fff"/><rect x="22.3" y="20" width="1.4" height="12" fill="#fff"/></svg>
  <span class="category-label">Heat Cantrol</span>
</div>

<div class="abs rule"></div>
<h1 class="abs welcome-title">Welcome to Casco Brew Works</h1>
<p class="abs welcome-text">Welcome to our Website. Are you looking for a Moonshine Still? Are you a Lavender Farm? Are you wanting to distill Essential Oils on your farm and make Hydrosols too? Do you want to make an Herbal Extraction or Tincture? Do you want to start a Home Business? Are you a Micro ( small) Distillery wanting a Set up? Are you a Race Car driver looking for alternative ways to get your Ethanol? Are you a Prepper? Are you interested in Making Alcohol in times of Survival? Do you need clean radiation free Water for your community? Do you want to support Local Farmers, get back to the Source and Nature? Are you a Canna-business</p>

<div class="abs section-divider" style="top:612px"></div>

<h2 class="abs section-title product-title">Our Product</h2>
<div class="abs product-underline"></div>
<svg class="abs" style="left:337px;top:644px" width="8" height="6" viewBox="0 0 8 6"><path d="M0 0h8L4 6z" fill="#4a1214"/></svg>

<svg class="abs" style="left:78px;top:721px" width="12" height="12" viewBox="0 0 12 12"><circle cx="6" cy="6" r="6" fill="#2a0a0b"/><path d="M7 3.5L4.5 6 7 8.5" stroke="#fff" stroke-width="1.6" fill="none"/></svg>
<svg class="abs" style="left:590px;top:721px" width="12" height="12" viewBox="0 0 12 12"><circle cx="6" cy="6" r="6" fill="#2a0a0b"/><path d="M5 3.5L7.5 6 5 8.5" stroke="#fff" stroke-width="1.6" fill="none"/></svg>

<div class="abs product-card" style="left:105px">
  <div class="product-image" role="img" aria-label="Copper column section with steel clamp" style="background:linear-gradient(135deg,#eeeeee,#c98a5a 60%,#e8e8e8)"></div>
  <div class="product-name">Home Distiller</div>
  <div class="product-desc">Lorem Ipsum is simply dummy text of the printing and typesetting industry</div>
  <div class="product-actions"><span>⚲ Detailes</span><span>🛒 Add to Cart</span></div>
</div>
<div class="abs product-card" style="left:226px">
  <div class="product-image" role="img" aria-label="Tall stainless steel still standing outdoors among greenery" style="background:linear-gradient(90deg,#5e7d2f,#b9b6a6 35%,#d7d4c6 55%,#6b8a35)"></div>
  <div class="product-name">Home Distiller</div>
  <div class="product-desc">Lorem Ipsum is simply dummy text of the printing and typesetting industry</div>
  <div class="product-actions"><span>⚲ Detailes</span><span>🛒 Add to Cart</span></div>
</div>
<div class="abs product-card" style="left:347px">
  <div class="product-image" role="img" aria-label="Stainless steel boiler keg with gauge" style="background:linear-gradient(90deg,#6f8b3a,#c8c8c4 30%,#e6e6e2 55%,#7a8f48)"></div>
  <div class="product-name">Home Distiller</div>
  <div class="product-desc">Lorem Ipsum is simply dummy text of the printing and typesetting industry</div>
  <div class="product-actions"><span>⚲ Detailes</span><span>🛒 Add to Cart</span></div>
</div>
<div class="abs product-card" style="left:469px">
  <div class="product-image" role="img" aria-label="Brass keg boiler with electric heating cord" style="background:linear-gradient(90deg,#ececec,#b8a878 40%,#8e8058 60%,#ececec)"></div>
  <div class="product-name">Home Distiller</div>
  <div class="product-desc">Lorem Ipsum is simply dummy text of the printing and typesetting industry</div>
  <div class="product-actions"><span>⚲ Detailes</span><span>🛒 Add to Cart</span></div>
</div>

<div class="abs section-divider" style="top:844px"></div>

<h2 class="abs section-title block-title" style="left:103px">How to Works</h2>
<div class="abs mini-arrows" style="left:396px"><svg width="8" height="8" viewBox="0 0 8 8"><circle cx="4" cy="4" r="4" fill="#2a0a0b"/><path d="M5 2L3 4l2 2" stroke="#fff" fill="none"/></svg><svg width="8" height="8" viewBox="0 0 8 8"><circle cx="4" cy="4" r="4" fill="#2a0a0b"/><path d="M3 2l2 2-2 2" stroke="#fff" fill="none"/></svg></div>
<div class="abs block-line" style="left:103px;width:313px"></div>

<div class="abs video" style="left:105px" role="img" aria-label="Video still of three men assembling an extraction rig"><div class="video-caption">Alcohol Extraction of Cannabis Oil</div><div class="video-play"></div><div class="video-bar"><i></i></div></div>
<div class="abs video" style="left:267px" role="img" aria-label="Video still of three men assembling an extraction rig"><div class="video-caption">Alcohol Extraction of Cannabis Oil</div><div class="video-play"></div><div class="video-bar"><i></i></div></div>

<h2 class="abs section-title block-title" style="left:429px">Our Blogs</h2>
<div class="abs mini-arrows" style="left:556px"><svg width="8" height="8" viewBox="0 0 8 8"><circle cx="4" cy="4" r="4" fill="#2a0a0b"/><path d="M5 2L3 4l2 2" stroke="#fff" fill="none"/></svg><svg width="8" height="8" viewBox="0 0 8 8"><circle cx="4" cy="4" r="4" fill="#2a0a0b"/><path d="M3 2l2 2-2 2" stroke="#fff" fill="none"/></svg></div>
<div class="abs block-line" style="left:429px;width:148px"></div>

<div class="abs blog-item" style="top:903px">
  <div class="blog-thumb" role="img" aria-label="Row of amber spirit bottles" style="background:linear-gradient(90deg,#8a5a3a,#d6a66a 50%,#7a4a2a)"></div>
  <div class="blog-text"><b>Lorem Ipsum is simply dummy</b><p>Lorem Ipsum is simply dummy text of the printing and typesetting industry.</p></div>
</div>
<div class="abs blog-item" style="top:962px">
  <div class="blog-thumb" role="img" aria-label="Blue-toned close up of distillation equipment" style="background:linear-gradient(135deg,#1f3c5a,#4e7aa0 50%,#1a2e44)"></div>
  <div class="blog-text"><b>Lorem Ipsum is simply dummy</b><p>Lorem Ipsum is simply dummy text of the printing and typesetting industry.</p></div>
</div>

<footer class="abs site-footer"></footer>

<div class="abs footer-col" style="left:105px">
  <div class="footer-title">Quick Links</div><div class="footer-line"></div>
  <div class="links"><span>Home</span><span>Shop</span><span>About Us</span><span>Blog</span><span>Contact Us</span><span>Books</span><span>Photos</span><span>Links</span><span>Videos</span><span>policy</span></div>
</div>
<div class="abs footer-col" style="left:227px">
  <div class="footer-title">Newslatter Signup</div><div class="footer-line"></div>
  <p class="footer-note">Lorem Ipsum is simply dummy text of the printing and typesetting industry.</p>
  <div class="field">Enter Your Name</div>
  <div class="field">Enter Email Address</div>
  <div class="subscribe">Subscribe</div>
</div>
<div class="abs footer-col" style="left:348px">
  <div class="footer-title">Latest News</div><div class="footer-line"></div>
  <div class="news" style="margin-top:11px"><div class="news-date"><b>15</b><span>May</span></div><div class="news-text"><b>Lorem Ipsum is simply dummy</b><p>Lorem Ipsum is simply dummy text of the printing and type-</p></div></div>
  <div class="news" style="margin-top:11px"><div class="news-date"><b>20</b><span>May</span></div><div class="news-text"><b>Lorem Ipsum is simply dummy</b><p>Lorem Ipsum is simply dummy text of the printing and type-</p></div></div>
</div>
<div class="abs footer-col" style="left:470px">
  <div class="footer-title">Contact Detailes</div><div class="footer-line"></div>
  <div class="phone" style="margin-top:10px"><svg width="5" height="8" viewBox="0 0 5 8"><rect x=".5" y=".5" width="4" height="7" rx=".8" fill="none" stroke="#fff"/></svg>555 204 3178.</div>
  <div class="phone"><svg width="5" height="8" viewBox="0 0 5 8"><rect x=".5" y=".5" width="4" height="7" rx=".8" fill="none" stroke="#fff"/></svg>555 317 6402</div>
  <div class="socials"><i></i><i></i><i></i><i></i></div>
</div>

</body>
</html>
```